Box Design for Flooring product

***IMPORTANT: PLEASE READ THE DOCUMENT PROVIDED WITH THIS BRIEF CAREFULLY BEFORE ACCEPTING THIS PROJECT***
Need a creative design for the packaging of a flooring product. The packaging is two boxes: one holding 36 planks of flooring, and the other 7 planks of flooring. There are 4 colours for the flooring planks that need a box designed (for both the 36 plank box and 7 plank box). The boxes measures 92 cm x 16cm x 7cm (36 planks) and 92 cm x 16cm x 1.5cm (7 planks).
More details are provided in the requirements document attached with this brief. Also attaching other supporting documents with this brief mentioned in the document.
Updates
Font styles to use
Other font styles liked:
- Montserrat-Regular
Look and feel
Each slider illustrates characteristics of the customer's brand and the style your logo design should communicate.

```html
<!DOCTYPE html>
<html lang="en">
<head>
<meta charset="utf-8">
<title>Velmora Flooring Box</title>
<link href="https://fonts.googleapis.com/css2?family=Montserrat:wght@400;500;600&display=swap" rel="stylesheet">
<style>
:root{
  --brown:#6e655a;
  --ink:#3d3935;
  --white:#ffffff;
  --backdrop:#d6d6d8;
  --floor:#c9a27a;
  --plank:#9a9794;
}
*{margin:0;padding:0;box-sizing:border-box}
html,body{width:1200px;height:768px;overflow:hidden}
body{background:var(--backdrop);font-family:'Montserrat',sans-serif;color:var(--ink);position:relative}
.box{position:absolute;left:102px;top:96px;width:980px;height:576px;box-shadow:0 4px 10px rgba(0,0,0,.25)}
.flap{position:absolute;left:0;top:0;width:980px;height:78px}
.front{position:absolute;left:0;top:78px;width:980px;height:174px;background:linear-gradient(100deg,#eeeeee 0%,#ffffff 30%);overflow:hidden}
.brand-name{position:absolute;left:162px;top:50px;font-size:60px;font-weight:500;color:var(--brown);letter-spacing:2px;line-height:1}
.brand-tag{position:absolute;left:164px;top:116px;font-size:13px;font-weight:500;color:var(--brown);letter-spacing:4.4px}
.plank-photo{position:absolute;left:566px;top:0;width:116px;height:158px;background:linear-gradient(90deg,#a9a7a4,#928f8c 50%,#a5a3a0)}
.room-photo{position:absolute;left:682px;top:0;width:298px;height:174px}
.band{position:absolute;left:0;width:980px;height:76px;background:var(--brown);color:var(--white)}
.band-top{top:252px;transform:rotate(180deg)}
.band-bottom{top:500px}
.features{position:absolute;left:93px;top:10px;list-style:none;font-size:6.5px;line-height:8.6px}
.features li::before{content:"";display:inline-block;width:3.5px;height:3.5px;border-radius:50%;background:var(--white);margin-right:4px;vertical-align:middle}
.band-top .features{font-size:5.6px;line-height:7.6px}
.band-logo{position:absolute;left:0;width:980px;top:14px;text-align:center}
.band-logo .name{font-size:30px;font-weight:500;letter-spacing:1px;line-height:1}
.band-logo .tag{font-size:8px;font-weight:500;letter-spacing:3px;margin-top:3px}
.cert{position:absolute;left:786px;top:8px;width:94px;height:62px;border:1px solid var(--white);padding:3px}
.cert-mark{width:86px;height:20px;border:1px solid var(--white);margin-bottom:2px}
.cert-row{display:flex;justify-content:space-between;font-size:3.6px;border-top:.5px solid var(--white);padding:1.5px 1px}
.instructions{position:absolute;left:0;top:328px;width:980px;height:172px;background:var(--white)}
.step{position:absolute;font-size:4.4px;line-height:5.2px;color:var(--ink)}
.step h3{font-size:7.4px;font-weight:500;line-height:8.4px;margin-bottom:2px}
.step-pic{position:absolute;width:54px;height:54px}
.pic-floor{background:linear-gradient(160deg,#ddd2c4,var(--floor))}
.pic-plank{background:linear-gradient(160deg,#c9c7c4,var(--plank))}
.pic-wall{background:linear-gradient(180deg,#f1efec 55%,#d8b68e)}
</style>
</head>
<body>
<div class="box">
  <svg class="flap" viewBox="0 0 980 78">
    <polygon points="0,78 18,2 962,2 980,78" fill="#fff" stroke="#555" stroke-width="1"/>
  </svg>

  <section class="front">
    <div class="brand-name">VELMORA</div>
    <div class="brand-tag">PREMIUM FLOORS AND TILES</div>
    <div class="plank-photo" role="img" aria-label="Photo of grey wood-effect flooring planks"></div>
    <svg class="room-photo" viewBox="0 0 298 174" role="img" aria-label="Photo of a bedroom with grey wood-effect floor">
      <defs>
        <linearGradient id="roomTone" x1="0" y1="0" x2="0" y2="1">
          <stop offset="0" stop-color="#eef0f2"/>
          <stop offset=".55" stop-color="#dfe2e6"/>
          <stop offset=".7" stop-color="#b9b6b2"/>
          <stop offset="1" stop-color="#8f8b87"/>
        </linearGradient>
      </defs>
      <path d="M18,174 C40,90 110,20 200,0 L298,0 L298,174 Z" fill="url(#roomTone)"/>
      <path d="M18,174 C40,90 110,20 200,0" fill="none" stroke="var(--brown)" stroke-width="4"/>
    </svg>
  </section>

  <section class="band band-top">
    <ul class="features">
      <li>Easy to lay</li>
      <li>Water resistant, easy to clean</li>
      <li>Ideal for Bathrooms and Kitchens</li>
      <li>Pack coverage 5m2 (36 per planks pack) - for 5m2 box</li>
      <li>Pack coverage 1m2 (7 planks per pack) - for 1m2 box</li>
      <li>Plank size 914mm x 152mm (36" x 6" approx.)</li>
      <li>Suitable for general domestic use</li>
    </ul>
    <div class="band-logo"><div class="name">VELMORA</div><div class="tag">PREMIUM FLOORS AND TILES</div></div>
    <div class="cert">
      <div class="cert-mark"></div>
      <div class="cert-row"><span>EN 14041, EN 13501-1, EN 717-1, EN 13893</span></div>
      <div class="cert-row"><span>Reaction to Fire</span><span>Bfl-S1</span></div>
      <div class="cert-row"><span>Emission of Formaldehyde</span><span>E1</span></div>
      <div class="cert-row"><span>Slipperiness</span><span>DS</span></div>
    </div>
  </section>

  <section class="instructions">
    <div class="step" style="left:29px;top:12px;width:85px"><h3>Step 1:<br>Tools Needed</h3>Tools Needed You will need:<br>1. Craft knife<br>2. Tape measure<br>3. Pencil<br>4. Right angle ruler<br>5. Long straight edge<br>6. Vacuum &amp; Brush</div>
    <div class="step-pic pic-floor" style="left:116px;top:12px" role="img" aria-label="Tools: tape measure, ruler, knife and pencil"></div>
    <div class="step" style="left:179px;top:12px;width:62px"><h3>Step 3:<br>Removing<br>Skirting board</h3>If needed, remove skirting boards in the room</div>
    <div class="step-pic pic-wall" style="left:248px;top:12px" role="img" aria-label="Removing a skirting board"></div>
    <div class="step" style="left:311px;top:12px;width:110px"><h3>Step 5:<br>Get ready to lay</h3>Once the floor has been primed and after a final vacuum for dust, you are ready to start. It is recommended that when laying the flooring, you start from the middle of the room and complete each section one at a time. For best results lay in a staggered pattern.</div>
    <div class="step-pic pic-floor" style="left:426px;top:12px" role="img" aria-label="Vacuuming the sub-floor"></div>
    <div class="step" style="left:490px;top:12px;width:76px"><h3>Step 7: Arrows on<br>the backing paper</h3>Before laying the planks, ensure the arrows on the backing paper point in the same direction</div>
    <div class="step-pic pic-wall" style="left:572px;top:12px" role="img" aria-label="Arrows printed on plank backing paper"></div>
    <div class="step" style="left:634px;top:12px;width:126px"><h3>Step 9: Laying the<br>remaining planks</h3>Continue positioning the planks until you've covered half the room, then do the other half. Fill the gaps at the edges last.</div>
    <div class="step-pic pic-plank" style="left:768px;top:12px" role="img" aria-label="Laid planks across the floor"></div>
    <div class="step" style="left:831px;top:12px;width:78px"><h3>Step 11: Breaking<br>the cut plank</h3>Break the plank by bending it at the cut line until it snaps.</div>
    <div class="step-pic pic-plank" style="left:914px;top:12px" role="img" aria-label="Snapping a cut plank"></div>

    <div class="step" style="left:29px;top:72px;width:160px"><h3>Step 2: Acclimatize your floor</h3>Leave your new planks in the room for 24-48 hours to acclimate. Your existing floor must be sound, dry and level. If you have a timber floor, screw down any loose boards and then lay hardboard or plywood over it. Do not lay planks directly on floorboards.</div>
    <div class="step-pic pic-plank" style="left:193px;top:72px" role="img" aria-label="Plank packs resting in the room"></div>
    <div class="step" style="left:253px;top:72px;width:56px"><h3>Step 4:<br>Planning your<br>remove</h3>Divide the room into 4 sections by drawing 2 perpendicular lines across the floor and use these lines as your guide to ensure you are laying the planks perfectly square.</div>
    <div class="step-pic pic-floor" style="left:316px;top:72px" role="img" aria-label="Guide lines drawn on the floor with a square"></div>
    <div class="step" style="left:376px;top:72px;width:122px"><h3>Step 6: Dry lay your planks</h3>Start at the centre line and dry-lay a row of planks from the line to one of the walls. Avoid a narrow gap at the wall by moving the start line back half a plank. Repeat towards the other two walls.</div>
    <div class="step-pic pic-plank" style="left:502px;top:72px" role="img" aria-label="Planks dry-laid on the floor"></div>
    <div class="step" style="left:562px;top:72px;width:52px"><h3>Step 8:<br>Laying the<br>first plank</h3>Peel the backing paper off the first plank and press its edge against the start line. Lower the rest of the plank onto the floor and press it down.</div>
    <div class="step-pic pic-plank" style="left:618px;top:72px" role="img" aria-label="Pressing the first plank into place"></div>
    <div class="step" style="left:677px;top:72px;width:98px"><h3>Step 10:<br>Cutting the planks</h3>To cut planks for the gaps at the skirting, place the plank to be cut exactly on top of the last full plank. Mark the edge with a pencil, then cut along the line with a craft knife.</div>
    <div class="step-pic pic-plank" style="left:781px;top:72px" role="img" aria-label="Scoring a plank with a knife and straight edge"></div>
    <div class="step" style="left:841px;top:72px;width:66px"><h3>Step 12:<br>Laying the cut<br>planks</h3>With the backing paper still on, check that the cut plank fits into the gap. Then remove the paper and stick it in place. Repeat around the edge of the floor.</div>
    <div class="step-pic pic-plank" style="left:914px;top:72px" role="img" aria-label="Fitting a cut plank at the wall"></div>
  </section>

  <section class="band band-bottom">
    <ul class="features">
      <li>Easy to lay</li>
      <li>Water resistant, easy to clean</li>
      <li>Ideal for Bathrooms and Kitchens</li>
      <li>Pack coverage 5m2 (36 per planks pack) - for 5m2 box</li>
      <li>Pack coverage 1m2 (7 planks per pack) - for 1m2 box</li>
      <li>Plank size 914mm x 152mm (36" x 6" approx.)</li>
      <li>Suitable for general domestic use</li>
    </ul>
    <div class="band-logo"><div class="name">VELMORA</div><div class="tag">PREMIUM FLOORS AND TILES</div></div>
    <div class="cert">
      <div class="cert-mark"></div>
      <div class="cert-row"><span>EN 14041, EN 13501-1, EN 717-1, EN 13893</span></div>
      <div class="cert-row"><span>Reaction to Fire</span><span>Bfl-S1</span></div>
      <div class="cert-row"><span>Emission of Formaldehyde</span><span>E1</span></div>
      <div class="cert-row"><span>Slipperiness</span><span>DS</span></div>
    </div>
  </section>
</div>
</body>
</html>
```